BGC Business Card

Looking for a business card design to incorporate our branding. We want to only use the colors listing in the Branding Package (attached).
Updates

Target Market(s)

People who need their phone or device fixed.

Industry/Entity Type

Electronics

Contact Information for Business Card

Please use:

Brightwick Gadget Clinic LLC
4810 E Harlow Ridge Rd
Suite 417
San Antonio, TX 78163

Marcus Delgrove, Store Manager

(210) 555-0147

Requirements
Must have
• Must include the colors that are contained within the Branding Package PDF file.

```html
<!DOCTYPE html>
<html lang="en">
<head>
<meta charset="utf-8">
<title>Brightwick Gadget Clinic Business Card</title>
<link href="https://fonts.googleapis.com/css2?family=Source+Sans+3:wght@400;600&display=swap" rel="stylesheet">
<style>
  :root {
    --stage: #000000;
    --brand-orange: #ff5000;
    --card-light: #f4f4f4;
    --white: #ffffff;
  }
  html, body {
    margin: 0;
    padding: 0;
    width: 1200px;
    height: 900px;
    overflow: hidden;
    background: var(--stage);
    font-family: "Source Sans 3", sans-serif;
  }
  .canvas {
    position: relative;
    width: 1200px;
    height: 900px;
  }
  .card {
    position: absolute;
    top: 200px;
    width: 310px;
    height: 502px;
    box-sizing: border-box;
  }
  .card-front {
    left: 265px;
    background: var(--brand-orange);
    border-radius: 72px 0 72px 0;
    color: var(--white);
  }
  .card-back {
    left: 640px;
    background: var(--card-light);
    border-radius: 0 72px 0 72px;
  }
  .brand-tile {
    position: absolute;
    left: 151px;
    top: 73px;
    width: 124px;
    height: 124px;
    border-radius: 20px;
    background: var(--white);
    display: flex;
    align-items: center;
    justify-content: center;
    color: var(--brand-orange);
    font-weight: 600;
    font-size: 34px;
    letter-spacing: 1px;
  }
  .contact {
    position: absolute;
    left: 31px;
    top: 305px;
  }
  .contact-name {
    margin: 0;
    font-size: 19px;
    font-weight: 600;
    line-height: 24px;
  }
  .contact-title {
    margin: 1px 0 0;
    font-size: 13px;
    line-height: 18px;
  }
  .contact-phone {
    margin: 17px 0 0;
    font-size: 13px;
    line-height: 18px;
    display: flex;
    align-items: center;
    gap: 7px;
  }
  .contact-phone svg { width: 10px; height: 10px; }
  .company {
    margin: 20px 0 0;
    font-size: 13px;
    line-height: 21px;
  }
  .company-name { font-weight: 600; display: block; }
  .back-name {
    position: absolute;
    left: 157px;
    top: 182px;
    width: 300px;
    margin-left: -150px;
    transform: rotate(-90deg);
    text-align: center;
    color: var(--brand-orange);
    font-size: 27px;
    line-height: 36px;
    font-weight: 400;
    white-space: nowrap;
  }
  .back-square {
    position: absolute;
    left: 114px;
    top: 363px;
    width: 80px;
    height: 80px;
    border-radius: 9px;
    background: var(--brand-orange);
  }
</style>
</head>
<body>
<main class="canvas">
  <section class="card card-front">
    <div class="brand-tile">BGC</div>
    <div class="contact">
      <p class="contact-name">Marcus Delgrove</p>
      <p class="contact-title">Store Manager</p>
      <p class="contact-phone">
        <svg viewBox="0 0 10 10" aria-hidden="true"><path d="M2 0.5 L3.6 2.6 L2.7 3.6 Q3.8 5.9 6.3 7.2 L7.4 6.3 L9.5 7.9 L8.4 9.4 Q3.5 9 0.6 1.6 Z" fill="#ffffff"/></svg>
        (210) 555-0147
      </p>
      <p class="company">
        <span class="company-name">Brightwick Gadget Clinic LLC</span>
        4810 E Harlow Ridge Rd Suite<br>
        417 San Antonio, TX 78163
      </p>
    </div>
  </section>
  <section class="card card-back">
    <div class="back-name">Brightwick Gadget Clinic</div>
    <div class="back-square"></div>
  </section>
</main>
</body>
</html>
```